Summit Ridge Business Card

Side 1: Summit Ridge Logo (logo without Maltese cross) with industrial rope rescue related theme. Our company services - TRAINING - Fire Training, Confined Space Rescue Training, Rope Rescue training, Hazmat Training, Incident Command, EMS, Pump Operations Training. Website - summitridgeexample.com.
Side 2: Summit Ridge Fire Department Logo (logo with Maltese cross) with Firefighter related theme. Company (division) services - FIELD SERVICES - Fire Department, Stand-by Rescue, Safety, EMS, Planning. "Supporting the Emergency Response Community Since 1967"

Add contact information wherever it makes since (Name, Email, Phone).
I would like it to represent the Summit Ridge Fire Department Logo as a division not as a separate entity without saying it, possibly by depicting it in the background of Side 2 instead of being a standalone picture like the logo on Side 1.

```html
<!DOCTYPE html>
<html lang="en">
<head>
<meta charset="utf-8">
<title>Summit Ridge Business Card</title>
<link rel="stylesheet" href="https://fonts.googleapis.com/css2?family=Montserrat:wght@800&family=Open+Sans:wght@400;600;700&display=swap">
<style>
  :root {
    --red: #e81e25;
    --ink: #2b2b2b;
    --grey: #444446;
    --paper: #ffffff;
    --backdrop: #d9dadc;
  }
  * { box-sizing: border-box; margin: 0; padding: 0; }
  html, body { width: 1200px; height: 780px; overflow: hidden; }
  body {
    background: var(--backdrop);
    font-family: "Open Sans", Arial, sans-serif;
    color: var(--ink);
    position: relative;
  }
  .card {
    position: absolute;
    top: 230px;
    width: 560px;
    height: 320px;
    background: var(--paper);
    box-shadow: 0 6px 18px rgba(0,0,0,.18);
    overflow: hidden;
  }
  .card--contact { left: 26px; }
  .card--training { left: 614px; }

  /* Contact side */
  .brand { position: absolute; display: flex; align-items: center; gap: 8px; }
  .brand__dot { width: 14px; height: 14px; border-radius: 50%; background: var(--red); }
  .brand__name { font-weight: 700; color: var(--grey); letter-spacing: .06em; text-transform: uppercase; }
  .card--contact .brand { left: 34px; top: 30px; }
  .card--contact .brand__name { font-size: 19px; }

  .person { position: absolute; left: 34px; top: 78px; }
  .person__name { font-family: "Montserrat", Arial, sans-serif; font-weight: 800; font-size: 30px; line-height: 1; color: var(--ink); }
  .person__name .first { color: var(--red); }
  .person__title { font-size: 14px; margin-top: 4px; margin-left: 2px; }

  .services { position: absolute; left: 34px; top: 140px; width: 230px; }
  .services__heading { font-weight: 700; font-size: 14px; color: var(--red); letter-spacing: .02em; margin-bottom: 2px; }
  .services__list { list-style: none; }
  .services__list li { font-size: 13px; line-height: 20px; display: flex; justify-content: space-between; align-items: center; width: 165px; }
  .services__list li::after { content: ""; width: 9px; height: 9px; border-radius: 50%; background: var(--red); }

  .divider-v { position: absolute; left: 250px; top: 120px; width: 1px; height: 120px; background: #333; }

  .contact { position: absolute; left: 272px; top: 118px; font-size: 12.5px; line-height: 19px; }
  .contact__row { display: flex; align-items: center; gap: 7px; }
  .contact__row svg { width: 12px; height: 12px; flex: none; }
  .contact__row--plain { padding-left: 19px; }

  .band {
    position: absolute; left: 0; right: 0; bottom: 18px; height: 32px;
    background: var(--red); color: #fff;
    font-size: 14px; display: flex; align-items: center; justify-content: center;
    letter-spacing: .01em;
  }

  /* Training side */
  .card--training .brand { left: 0; right: 0; top: 62px; justify-content: center; gap: 12px; }
  .card--training .brand__dot { width: 26px; height: 26px; }
  .card--training .brand__name { font-size: 40px; color: var(--red); }

  .rule-head { position: absolute; left: 34px; right: 34px; top: 168px; display: flex; align-items: center; gap: 10px; }
  .rule-head::before, .rule-head::after { content: ""; flex: 1; height: 2px; background: var(--red); }
  .rule-head__label { font-weight: 700; font-size: 18px; color: var(--red); letter-spacing: .03em; }

  .training-list { position: absolute; left: 34px; right: 34px; top: 196px; list-style: none; display: flex; flex-wrap: wrap; column-gap: 14px; row-gap: 2px; font-size: 13.5px; justify-content: center; }
  .training-list li { display: flex; align-items: center; gap: 6px; white-space: nowrap; }
  .training-list li::before { content: ""; width: 9px; height: 9px; border-radius: 50%; background: var(--red); }

  .divider-h { position: absolute; left: 34px; right: 34px; top: 256px; height: 1px; background: linear-gradient(90deg, #888, #333, #888); }
  .website { position: absolute; left: 0; right: 0; top: 264px; text-align: center; font-size: 15px; letter-spacing: .02em; }
</style>
</head>
<body>

<section class="card card--contact" aria-label="Contact side">
  <div class="brand">
    <span class="brand__dot"></span>
    <span class="brand__name">Summit Ridge</span>
  </div>

  <div class="person">
    <p class="person__name"><span class="first">Marta</span> Kovalenko</p>
    <p class="person__title">Director</p>
  </div>

  <div class="services">
    <p class="services__heading">FIELD SERVICES</p>
    <ul class="services__list">
      <li>EMS</li>
      <li>Safety</li>
      <li>Planning</li>
      <li>Fire Department</li>
      <li>Stand-by Rescue</li>
    </ul>
  </div>

  <div class="divider-v"></div>

  <div class="contact">
    <p class="contact__row contact__row--plain">418 Harbor Lane</p>
    <p class="contact__row contact__row--plain">Port Arden, TX 77000</p>
    <p class="contact__row">
      <svg viewBox="0 0 12 12" aria-hidden="true"><path d="M2.5 1 4.3 1 5 3.4 3.9 4.3C4.5 5.7 6.3 7.5 7.7 8.1L8.6 7 11 7.7 11 9.5C11 10.4 10.3 11 9.5 11 5 11 1 7 1 2.5 1 1.7 1.6 1 2.5 1Z" fill="var(--red)"/></svg>
      (555) 014-2290
    </p>
    <p class="contact__row">
      <svg viewBox="0 0 12 12" aria-hidden="true"><rect x="1" y="2.5" width="10" height="7" rx="1" fill="var(--red)"/><path d="M1.5 3 6 6.5 10.5 3" stroke="#fff" stroke-width="1" fill="none"/></svg>
      info@summitridgeexample.com
    </p>
    <p class="contact__row">
      <svg viewBox="0 0 12 12" aria-hidden="true"><circle cx="6" cy="6" r="5" fill="var(--red)"/><path d="M1 6h10M6 1c-2.2 2.8-2.2 7.2 0 10M6 1c2.2 2.8 2.2 7.2 0 10" stroke="#fff" stroke-width=".8" fill="none"/></svg>
      www.summitridgeexample.com
    </p>
  </div>

  <p class="band">Supporting the Emergency Response Community Since 1967</p>
</section>

<section class="card card--training" aria-label="Training side">
  <div class="brand">
    <span class="brand__dot"></span>
    <span class="brand__name">Summit Ridge</span>
  </div>

  <div class="rule-head"><span class="rule-head__label">TRAINING</span></div>

  <ul class="training-list">
    <li>Fire Training</li>
    <li>Confined Space Rescue Training</li>
    <li>Rope Rescue training</li>
    <li>Hazmat Training</li>
    <li>Incident Command</li>
    <li>EMS</li>
    <li>Pump Operations Training</li>
  </ul>

  <div class="divider-h"></div>
  <p class="website">www.summitridgeexample.com</p>
</section>

</body>
</html>
```